FunBrixo Business Card

We need a business card design for our company. We sell construction-themed amusement rides for kids.

Contact Information for Business Card

Contact info on business card should include:
Carl Dunning
Co-Founder & COO
(833) 571-FUNBRIX
Carl@funbrixo-demo.com
www.funbrixo-demo.com

```html
<!DOCTYPE html>
<html lang="en">
<head>
<meta charset="utf-8">
<title>FunBrixo Business Card</title>
<link href="https://fonts.googleapis.com/css2?family=Arimo:wght@400;700&display=swap" rel="stylesheet">
<style>
  :root {
    --backdrop: #2b2b2b;
    --card-white: #ffffff;
    --brand-orange: #f0582a;
    --link-orange: #f07f22;
    --ink: #222222;
    --rule: #9a9a9a;
    --sky-top: #3f8ec4;
    --sky-mid: #a9c6d8;
    --horizon: #f3d6b8;
    --sand: #d49a55;
    --ride-orange: #f0a23a;
  }
  * { margin: 0; padding: 0; box-sizing: border-box; }
  html, body { width: 1200px; height: 1200px; overflow: hidden; }
  body {
    background: var(--backdrop);
    font-family: "Arimo", Arial, sans-serif;
    position: relative;
  }
  .card {
    position: absolute;
    top: 310px;
    height: 594px;
  }
  .card-front {
    left: 234px;
    width: 364px;
    background: var(--card-white);
    text-align: center;
  }
  .card-back {
    left: 627px;
    width: 369px;
    overflow: hidden;
  }
  .brand-name {
    position: absolute;
    left: 0; right: 0;
    top: 95px;
    font-size: 64px;
    font-weight: 700;
    line-height: 1;
    color: var(--brand-orange);
  }
  .person-name {
    position: absolute;
    left: 0; right: 0;
    top: 342px;
    font-size: 25px;
    font-weight: 700;
    color: var(--brand-orange);
  }
  .person-title {
    position: absolute;
    left: 0; right: 0;
    top: 371px;
    font-size: 18px;
    color: var(--ink);
  }
  .icon-row {
    position: absolute;
    left: 63px;
    top: 414px;
    width: 239px;
    height: 30px;
  }
  .contact-list {
    position: absolute;
    left: 0; right: 0;
    top: 463px;
    list-style: none;
    font-size: 19px;
    line-height: 27px;
    color: var(--ink);
  }
  .contact-list .accent { color: var(--link-orange); }
  .scene-photo {
    position: absolute;
    inset: 0;
    background: linear-gradient(180deg, var(--sky-top) 0%, var(--sky-mid) 35%, var(--horizon) 58%, var(--ride-orange) 72%, var(--sand) 100%);
  }
  .brand-name-reverse {
    position: absolute;
    left: 0; right: 0;
    top: 95px;
    text-align: center;
    font-size: 64px;
    font-weight: 700;
    line-height: 1;
    color: var(--card-white);
  }
</style>
</head>
<body>
  <section class="card card-front">
    <div class="brand-name">FunBrixo</div>
    <div class="person-name">CARL DUNNING</div>
    <div class="person-title">Co-Founder &amp; COO</div>
    <svg class="icon-row" viewBox="0 0 239 30" aria-hidden="true">
      <line x1="0" y1="15" x2="61" y2="15" stroke="var(--rule)" stroke-width="1"/>
      <line x1="178" y1="15" x2="239" y2="15" stroke="var(--rule)" stroke-width="1"/>
      <rect x="67" y="0" width="31" height="30" rx="2" fill="var(--brand-orange)"/>
      <rect x="104" y="0" width="31" height="30" rx="2" fill="var(--brand-orange)"/>
      <rect x="141" y="0" width="31" height="30" rx="2" fill="var(--brand-orange)"/>
      <!-- phone -->
      <path d="M73 12 q9.5 -6 19 0 l-1 3 h-4 v-2 h-9 v2 h-4 z" fill="#fff"/>
      <rect x="76" y="16" width="13" height="8" rx="1" fill="#fff"/>
      <circle cx="82.5" cy="20" r="2.2" fill="var(--brand-orange)"/>
      <!-- envelope -->
      <rect x="110" y="8" width="19" height="14" fill="none" stroke="#fff" stroke-width="1.8"/>
      <path d="M110 8 l9.5 8 l9.5 -8" fill="none" stroke="#fff" stroke-width="1.8"/>
      <!-- globe -->
      <circle cx="156.5" cy="15" r="9" fill="#fff"/>
      <path d="M151 10 q3 1 4 4 q-2 3 1 6 M158 8 q2 3 5 3 q0 4 -3 7" fill="none" stroke="var(--brand-orange)" stroke-width="1.6"/>
    </svg>
    <ul class="contact-list">
      <li>(833) 571-FUNBRIX</li>
      <li>Carl@funbrixo-demo.com</li>
      <li>www.<span class="accent">funbrixo-demo</span>.com</li>
    </ul>
  </section>

  <section class="card card-back">
    <div class="scene-photo" role="img" aria-label="Photo of a seaside play area with orange kids' excavator rides, fencing and a wheelbarrow under a blue evening sky"></div>
    <div class="brand-name-reverse">FunBrixo</div>
  </section>
</body>
</html>
```